Website for enterprise software start-up

We need a new Wordpress website. We are an early stage start-up focused on mobile video technology for cellular operators. The audience is strategy, marketing and customer acquisition execs from the operators.

The purpose of the site is to act as a sales brochure and capture leads. A demo app can be downloaded from the current site, want to put that behind a contact form.

Current website is at www.velmora.tv. Similar number of pages. Looking for a clean design template, with minimal customization. Blog will remain as is.

Want to be able to modify the copy via Wordpress. Reference designs I like: quandrix.com, briskfold7metrics.com

Target Market(s)

Mobile operators and MVNOs in the US and Asia Pacific regions

Industry/Entity Type

Business Software

Coding

Coded - Design and coding required

Number of Pages Required

4 page

Font styles to use
Sans Serif

Colors
f78f20

Requirements
Must have
• Form for downloading sample apps.
• Landing page with image, Product, Blog, About, Contact
• Team page

```html
<!DOCTYPE html>
<html lang="en">
<head>
<meta charset="utf-8">
<title>Velmora Media — Video Technology for Cellular Operators</title>
<link href="https://fonts.googleapis.com/css2?family=Open+Sans:wght@300;400;600;700&display=swap" rel="stylesheet">
<style>
:root{
  --orange:#f78f20;
  --orange-dark:#e07a10;
  --ink:#333;
  --muted:#777;
  --light:#f4f4f4;
  --line:#e3e3e3;
  --footer:#1e1e1e;
  --footer-deep:#141414;
  --white:#fff;
}
*{box-sizing:border-box;margin:0;padding:0}
html,body{width:1200px;height:2888px;overflow:hidden}
body{font-family:"Open Sans",Arial,sans-serif;color:var(--ink);background:var(--white);font-size:13px;line-height:1.6}
.page{position:relative;width:1200px;height:2888px}

/* header */
.site-header{height:70px;display:flex;align-items:center;justify-content:space-between;padding:0 40px 0 100px;background:var(--white);position:relative;z-index:2}
.brand{display:flex;align-items:center;gap:8px;background:var(--orange);color:var(--white);padding:8px 14px;font-weight:700;font-size:19px;letter-spacing:.5px}
.brand-square{width:14px;height:14px;background:var(--white)}
.nav{display:flex;align-items:center;height:70px}
.nav a{display:flex;align-items:center;height:70px;padding:0 20px;font-size:11px;font-weight:600;color:var(--ink);text-decoration:none;letter-spacing:.5px}
.nav a.active{background:var(--orange);color:var(--white)}
.nav .login{height:30px;margin-left:20px;padding:0 22px;background:var(--orange);color:var(--white);border-radius:2px}
.nav .search{margin-left:16px}

/* hero */
.hero{position:relative;height:490px}
.hero-photo{position:absolute;inset:0;background:linear-gradient(100deg,#d9c7b1 0%,#b89a7f 30%,#8b7564 55%,#a08f83 75%,#c7beb6 100%)}
.hero-copy{position:absolute;left:620px;top:110px;width:540px;color:var(--white)}
.hero-copy .lead{font-size:36px;font-weight:300;line-height:1.2;white-space:nowrap}
.hero-copy h1{font-size:40px;font-weight:700;line-height:1.2;letter-spacing:.5px;white-space:nowrap}
.hero-copy p{margin-top:14px;font-size:14px;opacity:.95;width:420px}
.btn{display:inline-block;background:var(--orange);color:var(--white);font-size:11px;font-weight:600;padding:11px 26px;border-radius:2px;letter-spacing:.5px}
.hero-copy .btn{margin-top:26px}
.hero-arrows{position:absolute;right:30px;bottom:20px;display:flex;gap:4px}
.hero-arrows span{width:26px;height:26px;background:rgba(0,0,0,.4)}

/* welcome */
.welcome{height:370px;padding:40px 150px 0;text-align:center}
.section-title{font-size:28px;font-weight:600;color:var(--ink)}
.welcome p{margin:14px auto 0;width:820px;font-size:12px;color:var(--muted)}
.features{display:flex;justify-content:space-between;margin-top:36px;text-align:left}
.feature{display:flex;gap:14px;width:270px}
.feature-icon{flex:none;width:54px;height:54px;border-radius:50%;background:var(--orange);display:flex;align-items:center;justify-content:center}
.feature h3{font-size:14px;font-weight:600;margin-bottom:4px}
.feature p{margin:0;width:auto;font-size:11px;color:var(--muted);text-align:left}
.feature p b{color:var(--orange);font-weight:600}

/* split bands */
.band{position:relative;height:450px;overflow:hidden;background:var(--orange)}
.band-photo{position:absolute;top:0;height:100%}
.band-copy{position:absolute;top:50px;width:400px;color:var(--white)}
.band-copy h2{font-size:26px;font-weight:600;margin-bottom:12px}
.band-copy .intro{font-size:12px;margin-bottom:16px;opacity:.95}
.ticks{list-style:none}
.ticks li{display:flex;align-items:flex-start;gap:12px;font-size:12px;margin-bottom:13px}
.ticks svg{flex:none;margin-top:2px}
.push .band-photo{left:520px;width:680px;background:linear-gradient(120deg,#9c9c9a 0%,#c9c6c0 40%,#e8e4dc 70%,#b8b2aa 100%);clip-path:polygon(60px 0,100% 0,100% 100%,60px 100%,0 50%)}
.push .band-copy{left:100px}
.native .band-photo{left:0;width:600px;background:linear-gradient(110deg,#5a4232 0%,#8a6a52 40%,#b59a80 70%,#7d6452 100%);clip-path:polygon(0 0,540px 0,600px 50%,540px 100%,0 100%)}
.native .band-copy{left:650px;top:80px;width:460px}

/* team */
.team{height:370px;padding-top:40px;text-align:center}
.team .sub{font-size:12px;color:var(--muted);margin-top:8px}
.members{display:flex;justify-content:center;gap:70px;margin-top:34px}
.member{width:160px}
.member-photo{width:130px;height:130px;border-radius:50%;margin:0 auto;border:4px solid var(--white);box-shadow:0 0 0 1px var(--line);background:linear-gradient(160deg,#c8ccd2,#8d939b)}
.member h4{font-size:13px;font-weight:600;color:var(--orange);margin-top:14px}
.member span{font-size:11px;color:var(--muted)}

/* partners */
.partners{height:195px;background:var(--light);display:flex;align-items:center;justify-content:center;gap:26px}
.partner{width:160px;height:84px;background:var(--white);border:1px solid var(--line);display:flex;align-items:center;justify-content:center}
.partner i{display:block;width:100px;height:22px;border-radius:3px;background:#c9c9c9}
.arrow{width:30px;height:30px;display:flex;align-items:center;justify-content:center}

/* footer */
.site-footer{height:460px;background:var(--footer);color:#bbb;padding:30px 100px 0}
.footer-top{display:flex;justify-content:space-between;align-items:center;padding-bottom:22px;border-bottom:1px solid #333}
.social{display:flex;gap:8px}
.social span{width:26px;height:26px;border-radius:50%;border:1px solid #777}
.footer-cols{display:flex;gap:60px;margin-top:36px}
.footer-cols h5{font-size:16px;font-weight:600;color:var(--white);margin-bottom:16px}
.apps{width:230px}
.store{width:150px;height:46px;border:1px solid #888;border-radius:6px;background:#000;margin-bottom:14px}
.location{width:230px;font-size:12px}
.location li{list-style:none;display:flex;gap:10px;margin-bottom:10px}
.contact-form{flex:1;display:grid;grid-template-columns:1fr 1fr;gap:10px 12px;align-content:start}
.field{height:30px;background:var(--white);border-radius:2px;font-size:11px;color:#999;padding:6px 10px}
.field.message{grid-column:1/3;height:90px}
.contact-form .btn{grid-column:2/3;justify-self:center;margin-top:6px}
.copyright{height:33px;background:var(--footer-deep);color:#888;font-size:11px;text-align:center;line-height:33px}
</style>
</head>
<body>
<div class="page">

<header class="site-header">
  <div class="brand"><span class="brand-square"></span>Velmora Media</div>
  <nav class="nav">
    <a class="active" href="#">HOME</a>
    <a href="#">PRODUCT</a>
    <a href="#">BLOG</a>
    <a href="#">ABOUT</a>
    <a href="#">CONTACT</a>
    <a class="login" href="#">LOG IN</a>
    <svg class="search" width="14" height="14" viewBox="0 0 14 14"><circle cx="6" cy="6" r="4.5" fill="none" stroke="#555" stroke-width="1.6"/><line x1="9.3" y1="9.3" x2="13" y2="13" stroke="#555" stroke-width="1.6"/></svg>
  </nav>
</header>

<section class="hero">
  <div class="hero-photo" role="img" aria-label="Photo of a smiling woman looking at her smartphone outdoors"></div>
  <div class="hero-copy">
    <div class="lead">Video Technology for</div>
    <h1>CELLULAR OPERATORS</h1>
    <p>Engage and reward your subscribers with rich mobile video delivered straight to their devices.</p>
    <span class="btn">GET STARTED</span>
  </div>
  <div class="hero-arrows"><span></span><span></span></div>
</section>

<section class="welcome">
  <h2 class="section-title">Welcome to Velmora Media</h2>
  <p>Velmora Media builds mobile video technology that helps cellular operators grow revenue, cut churn and reach subscribers in new ways. Our platform turns the handset into a channel for rich, relevant video that people actually want to watch.</p>
  <p>We started Velmora Media to help mobile operators navigate the network, solving the technical challenges of delivering personalised and high quality mobile video experiences, while keeping costs low.</p>
  <div class="features">
    <div class="feature">
      <div class="feature-icon"><svg width="24" height="24" viewBox="0 0 24 24"><path d="M3 3h9l9 9-9 9-9-9z" fill="#fff"/><circle cx="8" cy="8" r="2" fill="#f78f20"/></svg></div>
      <div><h3>Value Exchange</h3><p>One of the smartest ways to win subscriber loyalty is to reward attention with real value. <b>more</b></p></div>
    </div>
    <div class="feature">
      <div class="feature-icon"><svg width="24" height="24" viewBox="0 0 24 24"><rect x="2" y="5" width="20" height="14" rx="2" fill="#fff"/><path d="M10 9l5 3-5 3z" fill="#f78f20"/></svg></div>
      <div><h3>Video Centric</h3><p>Video has a strong pull with subscribers and grows engagement on every handset. <b>more</b></p></div>
    </div>
    <div class="feature">
      <div class="feature-icon"><svg width="24" height="24" viewBox="0 0 24 24"><circle cx="6" cy="12" r="3" fill="#fff"/><circle cx="18" cy="5" r="3" fill="#fff"/><circle cx="18" cy="19" r="3" fill="#fff"/><path d="M6 12L18 5M6 12l12 7" stroke="#fff" stroke-width="2"/></svg></div>
      <div><h3>Distribution</h3><p>We are agnostic to video CDN and all network distribution options available today. <b>more</b></p></div>
    </div>
  </div>
</section>

<section class="band push">
  <div class="band-copy">
    <h2>Push Video Notifications</h2>
    <p class="intro">Personalised Dynamic Video content, delivered at the perfect moment, to every subscriber device.</p>
    <ul class="ticks">
      <li><svg width="16" height="16" viewBox="0 0 16 16"><circle cx="8" cy="8" r="7" fill="none" stroke="#fff" stroke-width="1.4"/><path d="M4.5 8.2l2.3 2.3 4.7-4.8" fill="none" stroke="#fff" stroke-width="1.6"/></svg>Reach your mobile audience with rich video on their lock screen.</li>
      <li><svg width="16" height="16" viewBox="0 0 16 16"><circle cx="8" cy="8" r="7" fill="none" stroke="#fff" stroke-width="1.4"/><path d="M4.5 8.2l2.3 2.3 4.7-4.8" fill="none" stroke="#fff" stroke-width="1.6"/></svg>Deliver offers, messaging and personalised content anytime.</li>
      <li><svg width="16" height="16" viewBox="0 0 16 16"><circle cx="8" cy="8" r="7" fill="none" stroke="#fff" stroke-width="1.4"/><path d="M4.5 8.2l2.3 2.3 4.7-4.8" fill="none" stroke="#fff" stroke-width="1.6"/></svg>Combine targeted video with real time network data signals.</li>
      <li><svg width="16" height="16" viewBox="0 0 16 16"><circle cx="8" cy="8" r="7" fill="none" stroke="#fff" stroke-width="1.4"/><path d="M4.5 8.2l2.3 2.3 4.7-4.8" fill="none" stroke="#fff" stroke-width="1.6"/></svg>Measure each view for reporting and campaign tuning.</li>
      <li><svg width="16" height="16" viewBox="0 0 16 16"><circle cx="8" cy="8" r="7" fill="none" stroke="#fff" stroke-width="1.4"/><path d="M4.5 8.2l2.3 2.3 4.7-4.8" fill="none" stroke="#fff" stroke-width="1.6"/></svg>Easily deliver a new viewing experience with little effort.</li>
    </ul>
  </div>
  <div class="band-photo" role="img" aria-label="Photo of hands typing on a laptop showing a video player, with a coffee cup on the desk"></div>
</section>

<section class="band native">
  <div class="band-photo" role="img" aria-label="Photo of a smiling woman in a café using her smartphone"></div>
  <div class="band-copy">
    <h2>Native Push Video</h2>
    <p class="intro">Personalised Dynamic Video content, stored locally in apps, and playable even offline.</p>
    <ul class="ticks">
      <li><svg width="16" height="16" viewBox="0 0 16 16"><circle cx="8" cy="8" r="7" fill="none" stroke="#fff" stroke-width="1.4"/><path d="M4.5 8.2l2.3 2.3 4.7-4.8" fill="none" stroke="#fff" stroke-width="1.6"/></svg>Give your audience new rich content with smooth quality playback.</li>
      <li><svg width="16" height="16" viewBox="0 0 16 16"><circle cx="8" cy="8" r="7" fill="none" stroke="#fff" stroke-width="1.4"/><path d="M4.5 8.2l2.3 2.3 4.7-4.8" fill="none" stroke="#fff" stroke-width="1.6"/></svg>Instant play, no buffering, full quality experience every time.</li>
      <li><svg width="16" height="16" viewBox="0 0 16 16"><circle cx="8" cy="8" r="7" fill="none" stroke="#fff" stroke-width="1.4"/><path d="M4.5 8.2l2.3 2.3 4.7-4.8" fill="none" stroke="#fff" stroke-width="1.6"/></svg>Content is pre-cached close to viewer devices for smooth viewing.</li>
      <li><svg width="16" height="16" viewBox="0 0 16 16"><circle cx="8" cy="8" r="7" fill="none" stroke="#fff" stroke-width="1.4"/><path d="M4.5 8.2l2.3 2.3 4.7-4.8" fill="none" stroke="#fff" stroke-width="1.6"/></svg>Reduce the network load by shifting traffic off peak.</li>
      <li><svg width="16" height="16" viewBox="0 0 16 16"><circle cx="8" cy="8" r="7" fill="none" stroke="#fff" stroke-width="1.4"/><path d="M4.5 8.2l2.3 2.3 4.7-4.8" fill="none" stroke="#fff" stroke-width="1.6"/></svg>Use our existing content management and hosting tools.</li>
    </ul>
  </div>
</section>

<section class="team">
  <h2 class="section-title">Our Team</h2>
  <p class="sub">Velmora Media's team combines deep expertise in mobile video, networks and operator business.</p>
  <div class="members">
    <div class="member"><div class="member-photo" role="img" aria-label="Portrait of team member Edwin"></div><h4>Edwin</h4><span>Chief Executive Officer</span></div>
    <div class="member"><div class="member-photo" role="img" aria-label="Portrait of team member Dorian"></div><h4>Dorian</h4><span>Chief Technology Officer</span></div>
    <div class="member"><div class="member-photo" role="img" aria-label="Portrait of team member Vaughn"></div><h4>Vaughn</h4><span>Head of Sales Asia</span></div>
    <div class="member"><div class="member-photo" role="img" aria-label="Portrait of team member Rowan"></div><h4>Rowan</h4><span>Head of Product</span></div>
  </div>
</section>

<section class="partners" aria-label="Partners">
  <span class="arrow"><svg width="12" height="20" viewBox="0 0 12 20"><path d="M10 2L2 10l8 8" fill="none" stroke="#999" stroke-width="2"/></svg></span>
  <div class="partner"><i></i></div>
  <div class="partner"><i></i></div>
  <div class="partner"><i></i></div>
  <div class="partner"><i></i></div>
  <div class="partner"><i></i></div>
  <span class="arrow"><svg width="12" height="20" viewBox="0 0 12 20"><path d="M2 2l8 8-8 8" fill="none" stroke="#999" stroke-width="2"/></svg></span>
</section>

<footer class="site-footer">
  <div class="footer-top">
    <div class="brand"><span class="brand-square"></span>Velmora Media</div>
    <div class="social"><span></span><span></span><span></span><span></span><span></span></div>
  </div>
  <div class="footer-cols">
    <div class="apps">
      <h5>Sample Apps</h5>
      <div class="store" role="img" aria-label="App store download badge"></div>
      <div class="store" role="img" aria-label="App store download badge"></div>
    </div>
    <div class="location">
      <h5>Our Location</h5>
      <ul>
        <li><svg width="12" height="16" viewBox="0 0 12 16"><path d="M6 0a6 6 0 0 0-6 6c0 4.5 6 10 6 10s6-5.5 6-10a6 6 0 0 0-6-6z" fill="#f78f20"/><circle cx="6" cy="6" r="2.2" fill="#1e1e1e"/></svg><span>Suite 14, 220 Harbour Lane<br>North Reach, CA 94010</span></li>
        <li><svg width="14" height="14" viewBox="0 0 14 14"><path d="M3 1l2.5 3-1.5 1.5a8 8 0 0 0 4.5 4.5L10 8.5l3 2.5-1.5 2.5C6 13 1 8 .5 2.5z" fill="#f78f20"/></svg><span>Phone: (+1) 555 0142 7788</span></li>
        <li><svg width="14" height="12" viewBox="0 0 14 12"><rect x="0" y="0" width="14" height="12" rx="1" fill="#f78f20"/><path d="M1 1l6 5 6-5" fill="none" stroke="#1e1e1e" stroke-width="1.3"/></svg><span>info@velmora.tv</span></li>
      </ul>
    </div>
    <form class="contact-form">
      <div class="field">Name</div>
      <div class="field">Email</div>
      <div class="field">Phone</div>
      <div class="field">Subject</div>
      <div class="field message">Message</div>
      <span class="btn">SEND MESSAGE</span>
    </form>
  </div>
</footer>
<div class="copyright">© 2016 Velmora All Rights Reserved</div>

</div>
</body>
</html>
```